Website redesign for e-commerce site slaaprust.com

We are a small online retail company in the Netherlands, selling duvets and pillows online. We are in this business since 2007. We sell (mainly) down duvets, aiming on the higher income classes.

Re-design of elements and pages in order to refresh the site and make it more consistent.

We are fairly content about our website. After two years of existence, it is time though to put some new insights in it, and to renew the various elements in one single design direction (unity).

Target Market(s)

Consumers, 30-50 years old, medium-higher income class

Industry/Entity Type

Business

Number of Pages Required

4 page

Font styles to use
Sans Serif
Other font styles liked:
• Does not need to change probably.

Colors
85cae6
34a6d7
0293ce
0655a3
3176b5
85abd3
cfdeed
cee9f5

Requirements
Must have
• - Keywords about design
• o Modern
• o Clear
• o Readable
• o Good usability
• o Converting
• Files to deliver:
• - .PSD file,
• - Every Page and Elements must be in separate layers.
Nice to have
• It's a redesign, so it should look like the old one :-)
Should not have
• Not to difficult.

```html
<!DOCTYPE html>
<html lang="nl">
<head>
<meta charset="utf-8">
<title>slaaprust.com</title>
<link href="https://fonts.googleapis.com/css2?family=Roboto:wght@300;400;500;700&display=swap" rel="stylesheet">
<style>
:root{
  --sky:#85cae6;--azure:#34a6d7;--blue:#0293ce;--navy:#0655a3;--steel:#3176b5;
  --haze:#85abd3;--mist:#cfdeed;--ice:#cee9f5;
  --text:#444;--muted:#8a8a8a;--line:#e1e1e1;--panel:#f3f3f3;--price:#e8741e;
}
*{box-sizing:border-box;margin:0;padding:0}
html,body{width:1200px;height:2428px;overflow:hidden}
body{font-family:"Roboto",Arial,sans-serif;color:var(--text);background:#fff;font-size:14px;position:relative}
.wrap{width:1000px;margin:0 auto;position:relative}
a{color:inherit;text-decoration:none}

.topbar{height:36px;background:var(--navy);color:#fff;font-size:12px}
.topbar .wrap{display:flex;justify-content:space-between;align-items:center;height:36px}
.topbar .call{display:flex;align-items:center;gap:8px}
.topbar nav{display:flex}
.topbar nav a{padding:0 14px;border-left:1px solid rgba(255,255,255,.3)}
.topbar nav a:first-child{border:none}

.header{height:120px;background:var(--blue)}
.header .wrap{display:flex;justify-content:space-between;align-items:center;height:120px}
.brand{display:flex;align-items:center;gap:12px;color:#fff;font-size:40px;font-weight:500;letter-spacing:-.5px}
.brand .mark{width:26px;height:26px;background:#fff}
.search{width:300px;height:40px;background:#fff;display:flex;align-items:center;justify-content:space-between;padding:0 14px;color:#aaa;font-size:13px}

.mainnav{height:60px;border-bottom:1px solid var(--line)}
.mainnav .wrap{display:flex;height:60px;align-items:center}
.mainnav a{font-size:13px;font-weight:500;color:#666;padding:0 24px;text-transform:uppercase;line-height:60px}
.mainnav a:first-child{color:var(--blue);padding-left:0;border-bottom:3px solid var(--blue);line-height:57px}

.showcase{margin-top:32px;display:flex;gap:10px;height:536px}
.sidebar{width:200px;border:1px solid var(--line)}
.sidebar .head{height:56px;display:flex;align-items:center;justify-content:space-between;padding:0 14px;color:#fff;font-weight:500;font-size:14px;background:var(--navy);white-space:nowrap}
.sidebar .head.tone2{background:var(--steel)}
.sidebar .head.tone3{background:var(--azure)}
.sidebar .head.tone4{background:var(--sky)}
.sidebar .head i{width:18px;height:18px;border-radius:50%;background:#fff;display:block;position:relative;flex:none}
.sidebar .head i::after{content:"";position:absolute;left:5px;top:5px;width:5px;height:5px;border-right:2px solid var(--navy);border-bottom:2px solid var(--navy);transform:rotate(-45deg)}
.sidebar ul{list-style:none}
.sidebar li{height:50px;border-bottom:1px solid var(--line);display:flex;align-items:center;padding:0 14px;font-size:12px;color:#555;white-space:nowrap}
.sidebar li::before{content:"›";color:var(--blue);margin-right:10px;font-size:16px}

.hero{flex:1;position:relative;background:linear-gradient(160deg,#bcd2e2 0%,#e9f0f5 45%,#d8e3ec 100%)}
.hero .promo{position:absolute;left:50%;top:50%;transform:translate(-50%,-50%);text-align:center;color:#fff;width:330px}
.hero .promo .big{background:var(--steel);font-size:46px;font-weight:700;padding:30px 0;white-space:nowrap}
.hero .promo .small{background:#2b3f55;font-size:11px;font-weight:500;padding:12px 10px;letter-spacing:.3px;white-space:nowrap}
.hero .dots{position:absolute;bottom:18px;left:50%;transform:translateX(-50%);display:flex;gap:8px}
.hero .dots span{width:9px;height:9px;border-radius:50%;background:rgba(255,255,255,.7)}
.hero .dots span:first-child{background:var(--blue)}

.usps{margin-top:32px;display:flex;gap:20px}
.usp{flex:1;height:100px;border:1px solid var(--line);display:flex;align-items:center;gap:18px;padding:0 24px;font-size:15px;color:#777;line-height:1.35}
.usp strong{color:var(--blue);font-size:19px;font-weight:500}

.products{margin-top:52px}
.products .bar{display:flex;justify-content:space-between;align-items:flex-end;border-bottom:2px solid var(--line);height:30px}
.products h2{font-size:14px;font-weight:500;color:var(--blue);text-transform:uppercase;border-bottom:2px solid var(--blue);margin-bottom:-2px;padding-bottom:6px}
.tabs{display:flex;margin-bottom:-2px}
.tabs span{font-size:13px;font-weight:500;color:var(--blue);padding:0 16px 6px}
.tabs span.on{border-bottom:2px solid var(--blue)}
.grid{display:flex;gap:40px;margin-top:40px}
.card{flex:1;text-align:center}
.card .photo{height:160px;background:radial-gradient(ellipse at center,#f1f3f5 0%,#dfe4e9 60%,#fff 100%)}
.card h3{font-size:15px;font-weight:400;color:#555;margin-top:26px;line-height:1.35;height:44px}
.card .price{font-size:22px;color:var(--price);margin-top:30px}
.card .btn{display:inline-block;margin-top:22px;background:var(--navy);color:#fff;font-size:12px;font-weight:500;padding:9px 16px}

.info{margin-top:56px;display:flex;gap:20px}
.infobox{flex:1;height:270px;background:var(--panel);border:1px solid var(--line);text-align:center;padding:34px 28px}
.infobox svg{display:block;margin:0 auto}
.infobox h4{color:var(--blue);font-size:18px;font-weight:400;margin-top:16px}
.infobox p{font-size:12px;color:#888;line-height:1.6;margin-top:12px}

.newsletter{margin-top:40px;height:200px;background:var(--azure);color:#fff;text-align:center;padding-top:56px}
.newsletter h4{font-size:18px;font-weight:500}
.newsletter form{display:flex;justify-content:center;margin-top:24px}
.newsletter .field{width:300px;height:42px;border:1px solid rgba(255,255,255,.7);display:flex;align-items:center;padding:0 14px;font-size:13px;color:#e8f5fb;text-align:left}
.newsletter .go{height:42px;background:var(--navy);display:flex;align-items:center;gap:8px;padding:0 18px;font-size:13px;font-weight:500}

.footer{margin-top:30px;background:var(--panel);height:340px;padding-top:44px}
.footer .cols{display:flex}
.footer .col{flex:1}
.footer h5{font-size:14px;font-weight:500;color:#333;margin-bottom:18px}
.footer li{list-style:none;font-size:12px;color:#777;margin-bottom:12px}
.footer .social{position:absolute;right:0;top:236px;display:flex;gap:10px}
.footer .social span{width:16px;height:16px;background:var(--navy);display:block}
.bottom{height:98px;background:#fff}
.bottom .wrap{display:flex;justify-content:space-between;align-items:center;height:98px}
.badges{display:flex;gap:12px;align-items:center}
.badges span{width:36px;height:24px;background:var(--mist);display:block}
.badges .seal{width:90px;height:44px;background:var(--haze)}
.bottom small{font-size:11px;color:#999}
</style>
</head>
<body>

<div class="topbar">
  <div class="wrap">
    <div class="call">
      <svg width="14" height="14" viewBox="0 0 24 24" fill="#fff"><path d="M6.6 10.8a15 15 0 0 0 6.6 6.6l2.2-2.2c.3-.3.7-.4 1-.2 1.1.4 2.300.6 3.6.6.6 0 1 .4 1 1V20c0 .6-.4 1-1 1A17 17 0 0 1 3 4c0-.6.4-1 1-1h3.5c.6 0 1 .4 1 1 0 1.3.2 2.5.6 3.6.1.3 0 .7-.2 1z"/></svg>
      <span>Bel voor persoonlijk advies · 071 - 234 56 78</span>
    </div>
    <nav><a>Over ons</a><a>Klantenservice</a><a>Contact</a></nav>
  </div>
</div>

<header class="header">
  <div class="wrap">
    <div class="brand"><span class="mark"></span>slaaprust.com</div>
    <div class="search"><span>Search items here</span>
      <svg width="16" height="16" viewBox="0 0 24 24" fill="none" stroke="#0293ce" stroke-width="2.5"><circle cx="10" cy="10" r="7"/><path d="M15 15l6 6"/></svg>
    </div>
  </div>
</header>

<nav class="mainnav">
  <div class="wrap"><a>Home</a><a>Advies</a><a>Onze bedden</a><a>Klantservice</a><a>Over ons</a><a>Winkelwagen</a></div>
</nav>

<div class="wrap">
  <section class="showcase">
    <aside class="sidebar">
      <div class="head">Dekbedden per merk <i></i></div>
      <ul>
        <li>Hofstede dekbedden</li>
        <li>Zachte Sneeuw dekbedden</li>
        <li>Almara dekbedden</li>
        <li>Bergveld dekbedden</li>
        <li>Veldhoven Wolk dekbedden</li>
      </ul>
      <div class="head tone2">Dekbedden per seizoen <i></i></div>
      <div class="head tone3">Donsdekens <i></i></div>
      <div class="head tone4">Overige dekbedden <i></i></div>
    </aside>
    <div class="hero" role="img" aria-label="Foto van een wit donsdekbed op een bed">
      <div class="promo">
        <div class="big">20% KORTING</div>
        <div class="small">OP DE COLLECTION VAN NACHTWOLKE SLAAPWAREN</div>
      </div>
      <div class="dots"><span></span><span></span><span></span><span></span></div>
    </div>
  </section>

  <section class="usps">
    <div class="usp">
      <svg width="40" height="40" viewBox="0 0 24 24" fill="none" stroke="#bbb" stroke-width="1.4"><path d="M6.6 10.8a15 15 0 0 0 6.6 6.6l2.2-2.2c.3-.3.7-.4 1-.2 1.1.4 2.3.6 3.6.6.6 0 1 .4 1 1V20c0 .6-.4 1-1 1A17 17 0 0 1 3 4c0-.6.4-1 1-1h3.5c.6 0 1 .4 1 1 0 1.3.2 2.5.6 3.6.1.3 0 .7-.2 1z"/></svg>
      <div>Persoonlijk advies<br>ma-vr 10-17 uur<br><strong>071 234 56 78</strong></div>
    </div>
    <div class="usp">
      <svg width="40" height="40" viewBox="0 0 24 24" fill="none" stroke="#bbb" stroke-width="1.4"><path d="M4 8l8-4 8 4v8l-8 4-8-4z"/><path d="M4 8l8 4 8-4M12 12v8"/></svg>
      <div>100 Dagen<br>Recht op retour!</div>
    </div>
    <div class="usp">
      <svg width="44" height="40" viewBox="0 0 26 24" fill="none" stroke="#bbb" stroke-width="1.4"><path d="M2 6h14v10H2zM16 10h5l3 3v3h-8z"/><circle cx="7" cy="18" r="2"/><circle cx="20" cy="18" r="2"/></svg>
      <div>Gratis verzending<br>binnen Europa</div>
    </div>
  </section>

  <section class="products">
    <div class="bar">
      <h2>Our products</h2>
      <div class="tabs"><span class="on">DUVETS</span><span>PILLOWS</span></div>
    </div>
    <div class="grid">
      <div class="card"><div class="photo" role="img" aria-label="Opgerold wit dekbed"></div><h3>Almara<br>Duinrand All Year</h3><div class="price">€ 99.00</div><a class="btn">Meer informatie</a></div>
      <div class="card"><div class="photo" role="img" aria-label="Gevouwen wit dekbed"></div><h3>Hofstede<br>Kroonlijn All Year</h3><div class="price">€ 175.20</div><a class="btn">Meer informatie</a></div>
      <div class="card"><div class="photo" role="img" aria-label="Wit dekbed met kussens"></div><h3>Almara<br>Veenhof All Year</h3><div class="price">€ 249.00</div><a class="btn">Meer informatie</a></div>
      <div class="card"><div class="photo" role="img" aria-label="Dekbed met blauw geruite bies"></div><h3>Veldhoven Wolk Stilte<br>Rustlijn All Year</h3><div class="price">€ 179.00</div><a class="btn">Meer informatie</a></div>
    </div>
  </section>

  <section class="info">
    <div class="infobox">
      <svg width="48" height="48" viewBox="0 0 24 24" fill="none" stroke="#bbb" stroke-width="1.3"><circle cx="12" cy="12" r="9"/><path d="M12 7v5l3 2"/></svg>
      <h4>Levertijden</h4>
      <p>Alle slaaprust.com modellen worden op voorraad gehouden. Vandaag besteld is morgen in huis, zeven dagen per week.</p>
    </div>
    <div class="infobox">
      <svg width="52" height="48" viewBox="0 0 26 24" fill="none" stroke="#bbb" stroke-width="1.3"><path d="M2 6h14v10H2zM16 10h5l3 3v3h-8z"/><circle cx="7" cy="18" r="2"/><circle cx="20" cy="18" r="2"/></svg>
      <h4>Verzending</h4>
      <p>Wij verzenden gratis binnen Nederland en Europa. Uw bestelling wordt netjes verpakt en met zorg bij u bezorgd.</p>
    </div>
    <div class="infobox">
      <svg width="48" height="48" viewBox="0 0 24 24" fill="none" stroke="#bbb" stroke-width="1.3"><circle cx="12" cy="12" r="9"/><path d="M8 12.5l3 3 5-6"/></svg>
      <h4>Tevredenheid</h4>
      <p>Wij gaan voor honderd procent tevredenheid. Niet goed? Dan heeft u honderd dagen recht op retour.</p>
    </div>
  </section>
</div>

<section class="newsletter">
  <h4>Op de hoogte blijven van mooie aanbiedingen? Laat hier uw email achter</h4>
  <form>
    <div class="field">Enter the Email id</div>
    <div class="go">
      <svg width="14" height="12" viewBox="0 0 24 20" fill="none" stroke="#fff" stroke-width="2"><path d="M2 2h20v16H2zM2 2l10 8 10-8"/></svg>
      SUBSCRIBE
    </div>
  </form>
</section>

<footer class="footer">
  <div class="wrap">
    <div class="cols">
      <div class="col"><h5>Aankoop informatie</h5><ul><li>Actuele bestellijsten</li><li>Betaalproces</li><li>Over verzending</li><li>Service &amp; Garantie</li></ul></div>
      <div class="col"><h5>Organisatie</h5><ul><li>Klantenservice</li><li>Over ons</li><li>Klantbeoordelingen</li><li>Algemene Voorwaarden</li></ul></div>
      <div class="col"><h5>Onze webshops</h5><ul><li>slaaprust.com</li><li>kussenrust.com</li><li>winterwarm.com</li><li>Contactgegevens</li></ul></div>
      <div class="col"><h5>Bezoek ons</h5><ul><li>slaaprust.com</li><li>Lindegracht 14 A</li><li>2311 KL Leiden</li><li>Telefoon: 071 234 56 78</li><li>E-mail: info@slaaprust.com</li></ul></div>
    </div>
    <div class="social"><span></span><span></span><span></span><span></span></div>
  </div>
</footer>

<div class="bottom">
  <div class="wrap">
    <div class="badges"><span></span><span></span><span></span><span class="seal"></span></div>
    <small>Alle rechten voorbehouden © 2007 - 2015 slaaprust.com</small>
  </div>
</div>

</body>
</html>
```